Need App for Impact Related Events

My app is to help with internal events. When you enter the prompted event code the next screen shows you everyone currently at the event. It will give you the ability to Start a conversation with someone you met at that event, or signal it is your turn to send a message. The next screen is a message thread with that person. I am looking for a design that incorporates the colors and ‘feel good’ emotion of our logo. I have pieced together a pretty good interpretation of what I’m looking for in the attached mockup by slicing and dicing designs. I also attached our logo mascot.Screens (see attached mockups)

Note 1: I do not like the picture on the screen used in screen one because it makes it seem like a dating app. I attached an alternative photo that can be used or present different ideas.

Note 2: On the login/signup screen (screen 2) I need an additional first and last name for login, you can try to fit this on one login screen or present a two step signup screen where that is presented in the second screen.

READ MOCKUP GUIDELINES UNDER Must Haves

Target Market(s)

People attending internal social impact events

Industry/Entity Type

Charity

Font styles to use
Sans Serif

Colors
86cfc6

Requirements
Must have
• Follow the screen mockups attached to project
• PLEASE READ
• I have provided a relatively close design of what I’m looking for in the mockups. Some screens need to be followed more closely to my design mockup than other. I have listed a guide below how how closely you should follow my mockup design exactly. Overall I would like to see some ideas of incorporating a few accent colors so it doesn’t appear SO Blue. I also attached some app inspiration designs I found from around the web
• Screen Mockup Guideline Follow %
• Screen 1: 65% - mostly on target, would like to see ways to make it not SO Blue and possibly creative places to add some explainer text describing the app
• Screen 2: 50% - general design idea is here, but more open
• Screen 3: 35% - a lot more room for design influence
• Screen 4: 70% - mostly on target, a little room for design influence/color scheme ideas
• Screen 5-6: 25% - a lot of room for design change/ideas/influence
• Screen 7-8: 80% - already very close to what I need, maybe open to slight sizing and color scheme ideas
• Screen 9: 15% - the most open for influence, only the general functionality of the screen is communicated here
Nice to have
• Please Read Mockup Guideline above. In large part I am looking for something to use some nice accent colors so it is not overwhelmingly blue and bring the whole design into a seamless style.
Should not have

```html
<!DOCTYPE html>
<html lang="en">
<head>
<meta charset="utf-8">
<title>Kind Code – Create and Share</title>
<link href="https://fonts.googleapis.com/css2?family=Roboto:wght@300;400;500;700&display=swap" rel="stylesheet">
<style>
  :root {
    --page-bg: #ffffff;
    --screen-bg: #f5f5f5;
    --card-bg: #ffffff;
    --ink: #1c2430;
    --ink-soft: #3a3f47;
    --muted: #9a9a9a;
    --divider: #e3e3e3;
    --teal: #2ee6d2;
    --teal-deep: #16c2ae;
    --teal-text: #1fd6c2;
    --photo-top: #7fa6a6;
    --photo-mid: #5f8f8c;
    --photo-bottom: #3fe2cc;
  }
  * { box-sizing: border-box; margin: 0; padding: 0; }
  html, body { width: 1200px; height: 1200px; overflow: hidden; }
  body {
    background: var(--page-bg);
    font-family: "Roboto", sans-serif;
    color: var(--ink);
    position: relative;
  }
  .screen {
    position: absolute;
    top: 126px;
    width: 440px;
    height: 948px;
    background: linear-gradient(180deg, #f2f2f2 0%, #f7f7f7 60%, #ffffff 100%);
    border-radius: 40px;
    overflow: hidden;
    box-shadow: 0 0 0 1px #e6e6e6;
  }
  .screen--create { left: 130px; }
  .screen--code { left: 630px; }

  .status-bar {
    position: absolute; top: 0; left: 0; right: 0; height: 60px;
    background: #fff;
  }
  .status-bar__time {
    position: absolute; left: 40px; top: 20px;
    font-size: 15px; font-weight: 500;
  }
  .status-bar__icons { position: absolute; right: 26px; top: 22px; }

  .nav-bar {
    position: absolute; top: 60px; left: 0; right: 0; height: 47px;
    background: #fff;
    border-bottom: 1px solid var(--divider);
  }
  .nav-bar__back { position: absolute; left: 18px; top: 9px; }
  .nav-bar__title {
    text-align: center; font-size: 19px; font-weight: 400;
    letter-spacing: -0.3px; line-height: 47px; color: var(--ink-soft);
    margin-top: -6px;
  }

  .event-card {
    position: absolute; left: 18px; top: 131px; width: 402px;
    background: var(--card-bg);
    border-radius: 8px;
    overflow: hidden;
    box-shadow: 0 2px 10px rgba(0,0,0,0.03);
  }
  .event-card__photo {
    position: relative; height: 266px;
    background: linear-gradient(180deg, var(--photo-top) 0%, var(--photo-mid) 55%, var(--photo-bottom) 100%);
  }
  .event-card__identity {
    position: absolute; left: 24px; bottom: 12px;
    display: flex; align-items: center; gap: 12px;
  }
  .event-card__badge {
    width: 54px; height: 54px; border-radius: 50%;
    background: #fff;
  }
  .event-card__name { font-size: 24px; font-weight: 400; color: var(--ink); }
  .event-card__edit { margin-left: 2px; }
  .event-card__body { padding: 22px 24px 36px; }

  .field-label { font-size: 20px; font-weight: 400; color: var(--ink); }
  .text-field {
    margin-top: 28px; padding-bottom: 12px;
    border-bottom: 2px solid var(--teal-deep);
    font-size: 20px; font-weight: 300; color: var(--ink);
  }
  .text-field__hint { font-size: 17px; color: var(--muted); margin-left: 4px; }

  .code-value {
    margin-top: 14px;
    font-size: 28px; font-weight: 700; letter-spacing: 0.3px;
    color: var(--teal-text);
  }
  .code-divider {
    margin: 20px 0 24px;
    border-top: 2px dashed #d8d8d8;
  }
  .code-help {
    font-size: 21px; font-weight: 300; line-height: 28px;
    color: var(--ink); letter-spacing: -0.3px;
  }
  .event-card--code .event-card__body { padding: 22px 24px 40px; }

  .primary-button {
    position: absolute; height: 60px;
    background: var(--teal);
    border: none; border-radius: 4px;
    box-shadow: 0 4px 0 var(--teal-deep);
    color: #fff; font-family: "Roboto", sans-serif;
    font-size: 20px; font-weight: 500;
    display: flex; align-items: center; justify-content: center; gap: 14px;
  }
  .primary-button--get { left: 79px; top: 600px; width: 281px; }
  .primary-button--settings { left: 85px; top: 740px; width: 270px; font-weight: 400; }
</style>
</head>
<body>

  <section class="screen screen--create">
    <div class="status-bar">
      <span class="status-bar__time">9:41</span>
      <svg class="status-bar__icons" width="52" height="14" viewBox="0 0 52 14">
        <path d="M1 5 A10 10 0 0 1 17 5 M4 8 A6 6 0 0 1 14 8" stroke="#000" stroke-width="2" fill="none"/>
        <circle cx="9" cy="11.5" r="1.8"/>
        <rect x="25" y="2" width="23" height="11" rx="3" fill="none" stroke="#000" stroke-width="1.2"/>
        <rect x="27" y="4" width="19" height="7" rx="1.5"/>
        <rect x="49.5" y="5.5" width="1.5" height="4" rx="0.7"/>
      </svg>
    </div>
    <header class="nav-bar">
      <svg class="nav-bar__back" width="16" height="26" viewBox="0 0 16 26"><path d="M13 2 L3 13 L13 24" stroke="#2a2f36" stroke-width="2.4" fill="none" stroke-linecap="round"/></svg>
      <h1 class="nav-bar__title">Create a Kind Code</h1>
    </header>

    <article class="event-card">
      <div class="event-card__photo" role="img" aria-label="Photo of friends chatting over coffee at a cafe table">
        <div class="event-card__identity">
          <span class="event-card__badge"></span>
          <span class="event-card__name">Event Name</span>
          <svg class="event-card__edit" width="24" height="24" viewBox="0 0 24 24"><path d="M5 17 L16 6 L19 9 L8 20 L4 21 Z" fill="none" stroke="#1c2430" stroke-width="1.5"/><line x1="2" y1="23" x2="22" y2="23" stroke="#1c2430" stroke-width="1.5"/></svg>
        </div>
      </div>
      <div class="event-card__body">
        <p class="field-label">Give your location a name</p>
        <p class="text-field">Location Name <span class="text-field__hint">(Optional)</span></p>
      </div>
    </article>

    <button class="primary-button primary-button--get">GET YOUR CODE</button>
  </section>

  <section class="screen screen--code">
    <div class="status-bar">
      <span class="status-bar__time">9:41</span>
      <svg class="status-bar__icons" width="52" height="14" viewBox="0 0 52 14">
        <path d="M1 5 A10 10 0 0 1 17 5 M4 8 A6 6 0 0 1 14 8" stroke="#000" stroke-width="2" fill="none"/>
        <circle cx="9" cy="11.5" r="1.8"/>
        <rect x="25" y="2" width="23" height="11" rx="3" fill="none" stroke="#000" stroke-width="1.2"/>
        <rect x="27" y="4" width="19" height="7" rx="1.5"/>
        <rect x="49.5" y="5.5" width="1.5" height="4" rx="0.7"/>
      </svg>
    </div>
    <header class="nav-bar">
      <svg class="nav-bar__back" width="16" height="26" viewBox="0 0 16 26"><path d="M13 2 L3 13 L13 24" stroke="#2a2f36" stroke-width="2.4" fill="none" stroke-linecap="round"/></svg>
      <h1 class="nav-bar__title">Your Kind Code</h1>
    </header>

    <article class="event-card event-card--code">
      <div class="event-card__photo" role="img" aria-label="Photo of friends chatting over coffee at a cafe table">
        <div class="event-card__identity">
          <span class="event-card__badge"></span>
          <span class="event-card__name">Meet N Greet</span>
        </div>
      </div>
      <div class="event-card__body">
        <p class="field-label">Your Code</p>
        <p class="code-value">AA4367CN6734</p>
        <div class="code-divider"></div>
        <p class="code-help">Give this code to the people at your location or event to allow them to connect to each other - kind of like a wifi password</p>
      </div>
    </article>

    <button class="primary-button primary-button--settings">
      <svg width="30" height="30" viewBox="0 0 30 30">
        <g fill="#fff" transform="translate(15 15)">
          <rect x="-3" y="-14" width="6" height="7" rx="1"/>
          <rect x="-3" y="-14" width="6" height="7" rx="1" transform="rotate(45)"/>
          <rect x="-3" y="-14" width="6" height="7" rx="1" transform="rotate(90)"/>
          <rect x="-3" y="-14" width="6" height="7" rx="1" transform="rotate(135)"/>
          <rect x="-3" y="-14" width="6" height="7" rx="1" transform="rotate(180)"/>
          <rect x="-3" y="-14" width="6" height="7" rx="1" transform="rotate(225)"/>
          <rect x="-3" y="-14" width="6" height="7" rx="1" transform="rotate(270)"/>
          <rect x="-3" y="-14" width="6" height="7" rx="1" transform="rotate(315)"/>
          <circle r="9"/>
        </g>
        <circle cx="15" cy="15" r="4" fill="var(--teal)"/>
      </svg>
      Manage in settings
    </button>
  </section>

</body>
</html>
```